Corvel Capital LLC

Need Professional Business cards for New Investment Fund

Target Market(s)

High Quality investors

Industry/Entity Type

Financial

Contact Information for Business Card

Phone Number +1 555 284 6190
Name Lukas Varenko
Title Fund Manager
email lv@FundCorvel.com
Website www.FundCorvel.com

Colors

Designer to choose colors to be used in the design.

Requirements
Must have
• Must have our Logo and all of the above. Must be made so lettering and loge can be raised

```html
<!DOCTYPE html>
<html lang="en">
<head>
<meta charset="utf-8">
<title>Torvanel — Business Card</title>
<link rel="stylesheet" href="https://fonts.googleapis.com/css2?family=Questrial&display=swap">
<style>
  :root {
    --stage: #2b2b2d;
    --card-dark: #3b3b3d;
    --card-light: #ffffff;
    --accent: #35e02a;
    --mark-silver: #b9b9bb;
    --ink: #3c3c3c;
    --ink-soft: #6a6a6a;
    --rule: #9a9a9a;
  }
  * { box-sizing: border-box; margin: 0; padding: 0; }
  html, body {
    width: 1200px; height: 960px; overflow: hidden;
    background: var(--stage);
    font-family: "Questrial", "Century Gothic", sans-serif;
  }
  .stage {
    position: relative; width: 1200px; height: 960px;
    display: flex; flex-direction: column; align-items: center; justify-content: center;
    gap: 56px;
  }
  .card {
    position: relative; width: 630px; height: 360px;
    border-bottom: 5px solid var(--accent);
    border-left: 3px solid var(--accent);
  }
  .card--front { background: var(--card-dark); display: flex; align-items: center; justify-content: center; }
  .card--back { background: var(--card-light); display: flex; align-items: center; padding: 0 0 0 72px; }

  .brand { display: flex; align-items: center; gap: 12px; }
  .brand__square { width: 20px; height: 20px; flex: none; }
  .brand__name { font-size: 40px; font-weight: 400; letter-spacing: 1px; white-space: nowrap; }
  .card--front .brand__square { background: var(--mark-silver); }
  .card--front .brand__name { color: var(--mark-silver); }
  .card--back .brand__square { background: var(--accent); }
  .card--back .brand__name { color: var(--accent); }

  .divider { width: 1px; height: 150px; background: var(--rule); margin: 0 34px 0 40px; flex: none; }

  .details__name { color: var(--accent); font-size: 27px; font-weight: 400; line-height: 1.1; white-space: nowrap; }
  .details__title { color: var(--ink); font-size: 17px; margin-top: 4px; }
  .contacts { list-style: none; margin-top: 18px; }
  .contacts li { display: flex; align-items: center; gap: 10px; color: var(--ink-soft); font-size: 16px; line-height: 1.45; white-space: nowrap; }
  .contacts svg { width: 13px; height: 13px; fill: var(--accent); flex: none; }
</style>
</head>
<body>
<main class="stage">
  <section class="card card--front" aria-label="Card front">
    <div class="brand">
      <span class="brand__square"></span>
      <span class="brand__name">Torvanel</span>
    </div>
  </section>

  <section class="card card--back" aria-label="Card back">
    <div class="brand">
      <span class="brand__square"></span>
      <span class="brand__name">Torvanel</span>
    </div>
    <div class="divider"></div>
    <div class="details">
      <h1 class="details__name">Lukas Varenko</h1>
      <p class="details__title">Fund Manager</p>
      <ul class="contacts">
        <li>
          <svg viewBox="0 0 16 16" aria-hidden="true"><path d="M3.6 1.2l2.3 2.8-1.4 1.8c.9 2 2.4 3.6 4.4 4.6l1.7-1.4 2.9 2.2-1.2 2.6C7 13.6 2.3 8.9 1 3.2z"/></svg>
          +1 555 284 6190
        </li>
        <li>
          <svg viewBox="0 0 16 16" aria-hidden="true"><path d="M1 3h14v10H1z M2 4l6 5 6-5" stroke="#fff" stroke-width="1.2"/></svg>
          lv@FundCorvel.com
        </li>
        <li>
          <svg viewBox="0 0 16 16" aria-hidden="true"><circle cx="8" cy="8" r="7"/><path d="M1 8h14M8 1c-3 3-3 11 0 14M8 1c3 3 3 11 0 14" stroke="#fff" stroke-width="1" fill="none"/></svg>
          www.FundCorvel.com
        </li>
      </ul>
    </div>
  </section>
</main>
</body>
</html>
```